Craft brewery keg badge / badge branding to be on display on keg fonts in pubs and craft beer bars

We're a small craft beer producer and are looking to have a keg badge designed to be put onto keg fonts in bars as well as being used on our bottles. Our website is www.qelnoriales.co.uk. -Please take a look at our site however we're looking for new branding! We're not looking to have the windmill on the badge! We want a bold geometric hop design in the centre of the design. The beer is a low AVB beer (2.9% ABV) and will be hopped with Cascade, Colombus and Tarvel hops and will have a fruity / juicy aroma. We're looking to have a design that we can re-use again and again by changing: colours and wording for different beers in the future.

Target Market(s)
Craft beer drinkers
Industry/Entity Type
Craft Brewery
Requirements
Must have
- Simple, elegant, repeatable core message from the badge. It need a simple, bold geometric hop design (examples uploaded) in the centre which is repeatable across many brands in the future.
- The badge needs to be circular and 82mm across to fit our tap lenses (see http://www.vindex.co.uk/branding for the flat lens). The keg badge needs to be modern and in line with other keg badges like the examples attached- though we leave the artistic flair up to you guys. Please see below the styles of keg badge we like.
- Must be in vector file format and we must get a jpeg version too.

Should not have
- Should not be overcrowded and try to be too full of information. See attached examples.

```html
<!DOCTYPE html>
<html lang="en">
<head>
<meta charset="utf-8">
<title>Qelnoriales Craft Brewery – Keg Badge</title>
<link href="https://fonts.googleapis.com/css2?family=Black+Ops+One&family=Staatliches&display=swap" rel="stylesheet">
<style>
  :root {
    --page: #ffffff;
    --badge-red: #7a1316;
    --ray: #9b3a2f;
    --cream: #ecd7a4;
    --cream-deep: #d9bf86;
    --rope-light: #ead7a8;
    --rope-mid: #c9ad72;
    --rope-dark: #8a7145;
  }
  html, body {
    margin: 0;
    padding: 0;
    width: 1200px;
    height: 1200px;
    overflow: hidden;
    background: var(--page);
  }
  .keg-badge {
    display: block;
    width: 1200px;
    height: 1200px;
  }
  .badge-field { fill: var(--badge-red); }
  .sunburst line { stroke: var(--ray); stroke-width: 3; opacity: 0.7; }
  .rope-frame { fill: url(#ropeTone); stroke: var(--rope-dark); stroke-width: 4; }
  .hop-area { fill: url(#hopTone); }
  .headline {
    font-family: "Black Ops One", "Staatliches", sans-serif;
    font-size: 78px;
    letter-spacing: 3px;
    fill: var(--cream);
  }
  .est-label {
    font-family: "Staatliches", sans-serif;
    font-size: 44px;
    letter-spacing: 3px;
    fill: var(--cream);
  }
  .est-rule { stroke: var(--cream); stroke-width: 3; }
  .web-address {
    font-family: "Black Ops One", sans-serif;
    font-size: 37px;
    letter-spacing: 0;
    fill: var(--cream);
  }
  .strength {
    font-family: "Black Ops One", sans-serif;
    font-size: 34px;
    letter-spacing: 2px;
    fill: var(--cream);
  }
</style>
</head>
<body>
<svg class="keg-badge" viewBox="0 0 1200 1200" xmlns="http://www.w3.org/2000/svg">
  <defs>
    <radialGradient id="ropeTone" cx="50%" cy="50%" r="50%">
      <stop offset="86%" stop-color="#c9ad72"/>
      <stop offset="92%" stop-color="#ead7a8"/>
      <stop offset="100%" stop-color="#c9ad72"/>
    </radialGradient>
    <radialGradient id="hopTone" cx="50%" cy="45%" r="60%">
      <stop offset="0%" stop-color="#ecd7a4"/>
      <stop offset="100%" stop-color="#c99f78"/>
    </radialGradient>
    <path id="headlineArc" d="M 200 420 A 460 460 0 0 1 1000 420"/>
  </defs>

  <path class="rope-frame" role="img" aria-label="Twisted rope border around the badge"
        fill-rule="evenodd"
        d="M 600 20 A 580 580 0 1 1 599.9 20 Z M 600 92 A 508 508 0 1 0 600.1 92 Z"/>

  <circle class="badge-field" cx="600" cy="600" r="508"/>

  <g class="sunburst">
    <line x1="600" y1="340" x2="600" y2="140"/>
    <line x1="700" y1="360" x2="780" y2="170"/>
    <line x1="780" y1="420" x2="930" y2="270"/>
    <line x1="830" y1="500" x2="1020" y2="420"/>
    <line x1="840" y1="690" x2="1040" y2="760"/>
    <line x1="800" y1="780" x2="960" y2="900"/>
    <line x1="720" y1="850" x2="800" y2="1020"/>
    <line x1="480" y1="850" x2="400" y2="1020"/>
    <line x1="400" y1="780" x2="240" y2="900"/>
    <line x1="360" y1="690" x2="160" y2="760"/>
    <line x1="370" y1="500" x2="180" y2="420"/>
    <line x1="420" y1="420" x2="270" y2="270"/>
    <line x1="500" y1="360" x2="420" y2="170"/>
  </g>

  <text class="headline"><textPath href="#headlineArc" startOffset="50%" text-anchor="middle">CRAFT BREWERY</textPath></text>

  <rect class="hop-area" x="425" y="305" width="345" height="570" rx="36"
        role="img" aria-label="Bold geometric hop cone illustration with stem, drawn in cream line work"/>

  <line class="est-rule" x1="165" y1="548" x2="300" y2="548"/>
  <text class="est-label" x="232" y="592" text-anchor="middle">SINCE</text>
  <line class="est-rule" x1="165" y1="604" x2="300" y2="604"/>

  <line class="est-rule" x1="900" y1="548" x2="1045" y2="548"/>
  <text class="est-label" x="972" y="592" text-anchor="middle">1930</text>
  <line class="est-rule" x1="900" y1="604" x2="1045" y2="604"/>

  <text class="web-address" x="602" y="966" text-anchor="middle">QELNORIALES.CO.UK</text>
  <text class="strength" x="600" y="1060" text-anchor="middle">2.9% ABV</text>
</svg>
</body>
</html>
```